Moxy Fen needs some awesome stationary

Do you have what it takes to get my brand? You either do or you don't, have a crack at a design and you my just win my business.

I don't want to waste your or my time, so put your creative genius on either a business card or envelope.

I however need a package of stationary that follows the same brand. I will message you to complete the remaining should I like your first submission.

Here is what I need, have a go!

Basically I need the following for my small business based in melbourne.
- Letterhead (printer ready and MS Word)
- Business Card
- Compliments Slip
- Envelope
- Proposal Cover Page (MS Word only)
- Presentation Folder
- Marbled Fox Cards
- Student Name Tent
- Index Cards
- Vell-Ka

I am establishing the brand and it must be modern, professional but also relaxed; that is not formal and not corporate. It represents a company are leaders, but small enough to care and operate like a bunch of friends. We are bringing people and conversations back to business, and turfing out all the bureaucracy and crazy and wasteful procedures. Its about "lets talk and figure it out together and find even better ways".

Target Market(s)

Mainly companies that build software products, but Agile practices are used in many other industries (even graphic design projects)

Industry/Entity Type

Information Technology

Font styles to use
Sans Serif

Colors
3176b5
aaaaaa

Requirements
Must have
• I like curves and circles and not boxes or rectangles.
• I want a colour rich design with my brand colours, but it must be balanced.
• I want more modern than traditional, but simple modern
Should not have
• Not corporate
• Please don't waste my time if your not going to think about it.
• Don't mess with my primary logo
• Don't change my colours
• Don't overlay logo on image

```html
<!DOCTYPE html>
<html lang="en">
<head>
<meta charset="utf-8">
<title>Moxy Fen – Business Card</title>
<link rel="stylesheet" href="https://fonts.googleapis.com/css2?family=Open+Sans:wght@400;600;700&display=swap">
<style>
  :root {
    --brand-blue: #2b5aa2;
    --brand-grey: #949eae;
    --ink: #3d3d3d;
    --card-white: #ffffff;
    --backdrop: #e9e9e9;
    --rule: #c9c9c9;
  }
  * { margin: 0; padding: 0; box-sizing: border-box; }
  html, body {
    width: 1200px; height: 987px; overflow: hidden;
    background: var(--backdrop);
    font-family: "Open Sans", Arial, sans-serif;
  }
  .stage { position: relative; width: 1200px; height: 987px; }

  .card {
    position: absolute; left: 293px; width: 615px; height: 351px;
    box-shadow: 0 2px 6px rgba(0,0,0,0.18);
  }
  .card--front { top: 130px; background: var(--card-white); }
  .card--back  { top: 506px; background: var(--brand-blue); }

  /* Front: brand block */
  .brand {
    position: absolute; left: 40px; top: 88px; width: 240px;
    display: flex; flex-direction: column; align-items: center; gap: 14px;
  }
  .brand__dot {
    width: 96px; height: 96px; border-radius: 50%;
    background: var(--brand-blue);
  }
  .brand__name {
    font-size: 38px; font-weight: 600; color: var(--brand-blue);
    letter-spacing: 0.2px; line-height: 1;
  }

  .divider {
    position: absolute; left: 291px; top: 72px; width: 1px; height: 237px;
    background: var(--rule);
  }

  /* Front: contact block */
  .contact { position: absolute; left: 314px; top: 74px; color: var(--ink); }
  .contact__name {
    font-size: 21px; font-weight: 600; color: var(--brand-blue); line-height: 26px;
  }
  .contact__role {
    font-size: 16.5px; color: var(--brand-grey); line-height: 22px;
  }
  .contact__address {
    margin-top: 14px; font-size: 16px; line-height: 21px;
  }
  .contact__list { list-style: none; margin-top: 12px; }
  .contact__item {
    display: flex; align-items: center; gap: 8px;
    font-size: 16px; line-height: 23.5px;
  }
  .contact__icon { width: 15px; height: 15px; fill: var(--brand-blue); flex: none; }

  /* Back */
  .back-mark {
    position: absolute; left: 0; right: 0; top: 88px;
    display: flex; flex-direction: column; align-items: center; gap: 16px;
  }
  .back-mark__dot {
    width: 110px; height: 110px; border-radius: 50%;
    background: var(--brand-grey);
  }
  .back-mark__name {
    font-size: 40px; font-weight: 600; color: var(--card-white); line-height: 1;
  }
  .back-web {
    position: absolute; left: 0; right: 0; top: 296px; text-align: center;
    color: var(--card-white); font-size: 16px; letter-spacing: 5px;
  }
</style>
</head>
<body>
<main class="stage">
  <section class="card card--front" aria-label="Business card front">
    <div class="brand">
      <div class="brand__dot"></div>
      <div class="brand__name">Moxy Fen</div>
    </div>

    <div class="divider"></div>

    <div class="contact">
      <p class="contact__name">Dale Corwin</p>
      <p class="contact__role">CEO, Professional Scrum Trainer</p>
      <p class="contact__address">PO Box 4410<br>Larkfield Vale<br>VIC 3190, Australia</p>
      <ul class="contact__list">
        <li class="contact__item">
          <svg class="contact__icon" viewBox="0 0 16 16" aria-hidden="true"><path d="M3.6 1.2l2.3 2.7-1.3 1.8c.9 2 2.6 3.7 4.6 4.6l1.8-1.3 2.7 2.3-1.2 2.3C7.3 13.4 2.6 8.7 1.3 3.5z"/></svg>
          1300MOXYFEN
        </li>
        <li class="contact__item">
          <svg class="contact__icon" viewBox="0 0 16 16" aria-hidden="true"><path d="M4.5 0.5h7a1 1 0 0 1 1 1v13a1 1 0 0 1-1 1h-7a1 1 0 0 1-1-1v-13a1 1 0 0 1 1-1zm0.8 2v9.5h5.4V2.5zM8 12.8a0.9 0.9 0 1 0 0 1.8a0.9 0.9 0 0 0 0-1.8z"/></svg>
          +61 400 555 218
        </li>
        <li class="contact__item">
          <svg class="contact__icon" viewBox="0 0 16 16" aria-hidden="true"><path d="M1 3.5h14v1L8 9 1 4.5zM1 6l7 4.5L15 6v6.5H1z"/></svg>
          dale@moxy-fen.com.au
        </li>
        <li class="contact__item">
          <svg class="contact__icon" viewBox="0 0 16 16" aria-hidden="true"><path d="M8 1a7 7 0 1 0 0 14A7 7 0 0 0 8 1zm-1 2.2c-.6.8-1.6 1-1.3 2 .3.9 1.7.6 1.8 1.7.1 1-1.3 1.2-1 2.4.2 1 1 1.6.6 3.4A5 5 0 0 1 3 6.2zM9.5 13c.2-1.3 1.4-2 1.2-3.2-.2-1-1.5-1-1.6-2 0-1 1.5-1.4 1.3-2.6l-.1-.6A5 5 0 0 1 9.5 13z"/></svg>
          www.moxy-fen.com.au
        </li>
      </ul>
    </div>
  </section>

  <section class="card card--back" aria-label="Business card back">
    <div class="back-mark">
      <div class="back-mark__dot"></div>
      <div class="back-mark__name">Moxy Fen</div>
    </div>
    <p class="back-web">www.moxy-fen.com.au</p>
  </section>
</main>
</body>
</html>
```